IT Company requires new Business Card design.

Over the years we have had a few different business card designs. We are now due for new cards across the board for all staff. We felt this would be a good time to start fresh with a new design. Our traditional card simply had our details on the front, and a list of services on the back. We don't particularly need the list of services, we have had cards where the only thing on the rear of the card was our logo.
Feel free to be creative, we would like our tag line "Complete IT Management" to appear at some point, doesn't necessarily have to be with the logo.
I have attached samples and drafts of various previous cards we have used over the years.

```html
<!DOCTYPE html>
<html lang="en">
<head>
<meta charset="utf-8">
<title>Harbour Systems – Business Card</title>
<link rel="stylesheet" href="https://fonts.googleapis.com/css2?family=Roboto:wght@400;500;700;900&display=swap">
<style>
  :root {
    --bg: #e9e7e4;
    --ink: #5b6c7b;
    --ink-soft: #6e7d8a;
    --metal-light: #f4f5f6;
    --metal-mid: #dcdfe2;
    --metal-dark: #c7cbcf;
    --rule: #8a96a1;
  }
  * { box-sizing: border-box; margin: 0; padding: 0; }
  html, body { width: 1200px; height: 720px; overflow: hidden; background: var(--bg); }
  body { font-family: "Roboto", Arial, sans-serif; color: var(--ink); }

  .canvas {
    width: 1200px; height: 720px;
    display: flex; align-items: center; justify-content: center; gap: 50px;
  }

  .card {
    position: relative;
    width: 540px; height: 309px;
    border-radius: 4px;
    overflow: hidden;
    background:
      repeating-linear-gradient(0deg, rgba(255,255,255,0.35) 0 1px, rgba(0,0,0,0.025) 1px 3px),
      linear-gradient(160deg, var(--metal-light) 0%, var(--metal-mid) 45%, var(--metal-light) 70%, var(--metal-dark) 100%);
    box-shadow: 0 2px 6px rgba(0,0,0,0.18);
  }

  /* Front */
  .brand {
    position: absolute; left: 36px; top: 40px;
    display: flex; align-items: center; gap: 14px;
  }
  .brand-square { width: 64px; height: 64px; background: var(--ink); }
  .brand-name {
    font-weight: 900; font-size: 38px; line-height: 0.92;
    text-transform: uppercase; color: var(--ink); letter-spacing: -0.5px;
  }
  .divider {
    position: absolute; left: 0; right: 0; top: 148px;
    height: 1px; background: var(--rule); opacity: 0.6;
  }
  .person { position: absolute; right: 36px; top: 120px; text-align: left; width: 170px; }
  .person-name { font-weight: 700; font-size: 17px; color: var(--ink); margin-bottom: 10px; }
  .person-role { font-size: 12.5px; color: var(--ink-soft); }
  .address { position: absolute; right: 36px; top: 200px; font-size: 12.5px; line-height: 1.45; color: var(--ink-soft); text-align: right; }

  .contacts { position: absolute; left: 36px; bottom: 30px; list-style: none; font-size: 13px; color: var(--ink-soft); }
  .contacts li { display: flex; align-items: center; gap: 7px; line-height: 1.55; }
  .contacts svg { width: 11px; height: 11px; fill: var(--ink-soft); flex: none; }
  .contacts .pair { gap: 7px; }
  .contacts .pair svg + span + svg { margin-left: 8px; }

  /* Back */
  .back-lockup { position: absolute; left: 0; right: 0; top: 70px; text-align: center; }
  .back-name {
    font-weight: 900; text-transform: uppercase; color: var(--ink);
    font-size: 62px; line-height: 0.9; letter-spacing: -1px;
  }
  .back-name .line-2 { display: block; font-size: 44px; }
  .tagline {
    margin-top: 10px; font-weight: 400; font-size: 17px;
    letter-spacing: 5px; text-transform: uppercase; color: var(--ink-soft);
  }
  .back-web {
    position: absolute; left: 0; right: 0; bottom: 30px;
    text-align: center; font-weight: 500; font-size: 16px; letter-spacing: 1px; color: var(--ink-soft);
  }
</style>
</head>
<body>
<main class="canvas">

  <section class="card card-front" aria-label="Business card front">
    <div class="brand">
      <span class="brand-square"></span>
      <span class="brand-name">Harbour<br>Systems</span>
    </div>
    <div class="divider"></div>
    <div class="person">
      <p class="person-name">Daniel Hart</p>
      <p class="person-role">Operations Manager</p>
    </div>
    <p class="address">Unit 7 22 Marlowe Way<br>Kestrel WA 6100</p>

    <ul class="contacts">
      <li class="pair">
        <svg viewBox="0 0 12 12"><circle cx="6" cy="6" r="6"/></svg><span>08 9000 1234</span>
        <svg viewBox="0 0 12 12"><rect x="3" y="0" width="6" height="12" rx="1.5"/></svg><span>0400 123 456</span>
      </li>
      <li>
        <svg viewBox="0 0 12 12"><circle cx="6" cy="3.5" r="3"/><path d="M0 12a6 5 0 0 1 12 0z"/></svg><span>08 9000 1235</span>
      </li>
      <li>
        <svg viewBox="0 0 12 12"><rect x="0" y="2" width="12" height="8" rx="1"/></svg><span>daniel@harboursystems.com.au</span>
      </li>
      <li>
        <svg viewBox="0 0 12 12"><circle cx="6" cy="6" r="6"/></svg><span>www.harboursystems.com.au</span>
      </li>
    </ul>
  </section>

  <section class="card card-back" aria-label="Business card back">
    <div class="back-lockup">
      <p class="back-name">Harbour<span class="line-2">Systems</span></p>
      <p class="tagline">Complete IT Management</p>
    </div>
    <p class="back-web">www.harboursystems.com.au</p>
  </section>

</main>
</body>
</html>
```